RTavenor Business Cards & Letterhead

I have a logo but need a design for some new business cards. We are a Design-Build Firm that specializes in the design and construction of commercial projects.
the cards need to be professional. no cartoon stuff.
i would like to have the cards in AI format so I can update the card as needed. Logo is provided.
Our Address is: 4187 Marlowe Ct. Brookdale, Vermont 27614

```html
<!DOCTYPE html>
<html lang="en">
<head>
<meta charset="utf-8">
<title>RTavenor Business Card</title>
<link rel="stylesheet" href="https://fonts.googleapis.com/css2?family=Open+Sans:wght@400;600;800&display=swap">
<style>
  :root {
    --backdrop: #4a4a49;
    --card: #171717;
    --card-edge: #1565c0;
    --brand-blue: #0a72b8;
    --brand-blue-deep: #054a82;
    --brand-blue-light: #0a86d0;
    --wordmark-grey: #6f6f6f;
    --emboss: #262626;
    --text-light: #f2f2f2;
  }
  * { box-sizing: border-box; margin: 0; padding: 0; }
  html, body { width: 1200px; height: 801px; overflow: hidden; }
  body {
    background: var(--backdrop);
    font-family: "Open Sans", Arial, sans-serif;
    display: flex;
    align-items: center;
    justify-content: center;
    gap: 50px;
  }
  .card {
    position: relative;
    width: 540px;
    height: 310px;
    background: var(--card);
    border-radius: 16px;
    border-bottom: 3px solid var(--card-edge);
    border-left: 2px solid var(--card-edge);
    overflow: hidden;
  }
  .wordmark {
    font-weight: 800;
    letter-spacing: 1px;
    text-transform: uppercase;
    display: flex;
    align-items: center;
    gap: 10px;
    white-space: nowrap;
  }
  .wordmark sup { font-size: 0.35em; font-weight: 800; align-self: flex-start; margin-top: 0.3em; }
  .wordmark__square { width: 0.6em; height: 0.6em; background: currentColor; flex: none; }

  /* front */
  .card--front .wordmark {
    position: absolute; left: 30px; top: 34px;
    font-size: 34px; color: var(--wordmark-grey);
  }
  .card--front .wordmark__square { background: var(--brand-blue); }
  .edge-tab {
    position: absolute; left: 0; top: 118px;
    width: 16px; height: 46px; background: var(--brand-blue);
  }
  .person { position: absolute; left: 36px; top: 112px; }
  .person__name {
    color: var(--brand-blue); font-weight: 800; font-size: 22px; letter-spacing: 0.5px;
  }
  .person__role { color: var(--text-light); font-size: 16px; }
  .contact {
    position: absolute; left: 36px; top: 182px;
    list-style: none; color: var(--text-light); font-size: 14.5px; line-height: 21px;
  }
  .contact li { display: flex; align-items: center; gap: 8px; }
  .contact svg { width: 12px; height: 12px; fill: var(--brand-blue); flex: none; }
  .address {
    position: absolute; left: 36px; top: 252px;
    color: var(--text-light); font-size: 14.5px; line-height: 20px; font-style: normal;
  }
  .brand-panel {
    position: absolute; right: 30px; top: 60px;
    width: 170px; height: 196px; border-radius: 22px;
    background: linear-gradient(160deg, var(--brand-blue-light) 0%, var(--brand-blue) 45%, var(--brand-blue-deep) 100%);
  }

  /* back */
  .card--back { display: flex; align-items: center; justify-content: center; }
  .card--back .wordmark { font-size: 52px; color: var(--emboss); }
</style>
</head>
<body>
  <section class="card card--front" aria-label="Business card front">
    <div class="wordmark"><span class="wordmark__square"></span>RTavenor<sup>®</sup></div>
    <span class="edge-tab"></span>
    <div class="person">
      <p class="person__name">MARCUS HALE</p>
      <p class="person__role">Managing Director</p>
    </div>
    <ul class="contact">
      <li><svg viewBox="0 0 12 12"><path d="M2.4 0.6 4.3 2.8 3.3 4.3C4 5.8 6 7.8 7.7 8.7L9.2 7.7 11.4 9.6 10.3 11.4C5.5 11.4 0.6 6.5 0.6 1.7Z"/></svg>555 204 318</li>
      <li><svg viewBox="0 0 12 12"><path d="M0 2h12v8H0z M0 2l6 4.5L12 2" stroke="#171717" stroke-width="1"/></svg>info@tavenorbuild.com</li>
      <li><svg viewBox="0 0 12 12"><circle cx="6" cy="6" r="5.5"/><path d="M0.5 6h11M6 0.5c-3 3-3 8 0 11M6 0.5c3 3 3 8 0 11" stroke="#171717" stroke-width="0.9" fill="none"/></svg>www.tavenorbuild.com</li>
    </ul>
    <address class="address">4187 Marlowe Ct. Brookdale,<br>Vermont 27614</address>
    <div class="brand-panel" role="img" aria-label="Large brand symbol in blue"></div>
  </section>

  <section class="card card--back" aria-label="Business card back">
    <div class="wordmark"><span class="wordmark__square"></span>RTavenor<sup>®</sup></div>
  </section>
</body>
</html>
```